Business Cards Design for the electrical wholesaler: clean bold dynamic :)

We need a business card design that would follow our latest brand guidelines. As an electrical wholesaler we want to bring a fresh look and feel into the industry. The design should be clean bold and dynamic. It should come alive with the renewed energy of our green colour. Our grey colour should keep things balanced and complement the notion of maturity and responsibility. We employ Lato as a corporate font however are not bound by this font and we’re open to interpretation here.

Target Market(s)

Electrical contractors

Industry/Entity Type

Business

Contact Information for Business Card

Logo
Name & Surname: Halyna Dorosh
Job Title: Director of Marketing
Email: halya.dorosh@quillmail.example
Cell phone: XXX.XXX.XXXX
Address: 20517 - 87 Ave. Edmonton, AB, Canada. T6K 4N8
Business Phone: 780.555.0184
Website: www.brovix.example

Font styles to use
Other font styles liked:
• Lato

Requirements
Must have
• Logo & website
Nice to have
• Brand elements - some of them you may find in the attached Brand Guidelines (e.g. three lines on the background signifying "W")

```html
<!DOCTYPE html>
<html lang="en">
<head>
<meta charset="utf-8">
<title>Brovix Business Card</title>
<link href="https://fonts.googleapis.com/css2?family=Lato:wght@400;700&family=Exo+2:wght@600&family=Roboto:wght@400&display=swap" rel="stylesheet">
<style>
  :root {
    --backdrop: #3a3a3a;
    --card: #232323;
    --green: #7dc52a;
    --grey: #b4b4b4;
    --grey-dark: #3b3b3b;
    --white: #f2f2f2;
  }
  * { box-sizing: border-box; margin: 0; padding: 0; }
  html, body { width: 799px; height: 1200px; overflow: hidden; }
  body {
    background: var(--backdrop);
    display: flex;
    flex-direction: column;
    align-items: center;
    justify-content: space-around;
    padding: 60px 0;
  }
  .card {
    position: relative;
    width: 660px;
    height: 378px;
    border-radius: 26px;
    background: var(--card);
    overflow: hidden;
    box-shadow: 0 10px 28px rgba(0,0,0,.45);
  }

  /* Front */
  .front .brand {
    position: absolute;
    left: 0; right: 0; top: 140px;
    text-align: center;
  }
  .front .brand-name {
    font-family: "Lato", sans-serif;
    font-weight: 700;
    font-size: 88px;
    line-height: 1;
    color: var(--grey-dark);
    letter-spacing: 1px;
  }
  .front .brand-tag {
    font-family: "Lato", sans-serif;
    font-size: 15px;
    letter-spacing: 4px;
    color: var(--grey-dark);
    margin-top: 6px;
  }

  /* Back */
  .back .brand {
    position: absolute;
    left: 44px; top: 90px;
  }
  .back .brand-row { display: flex; align-items: center; gap: 14px; }
  .back .brand-mark {
    width: 46px; height: 46px;
    background: var(--green);
    border-radius: 4px;
  }
  .back .brand-name {
    font-family: "Lato", sans-serif;
    font-weight: 700;
    font-size: 70px;
    line-height: 1;
    color: var(--grey);
  }
  .back .brand-tag {
    font-family: "Lato", sans-serif;
    font-size: 12px;
    letter-spacing: 3.5px;
    color: var(--grey);
    margin-top: 6px;
  }
  .contact {
    position: absolute;
    left: 372px; top: 128px;
    font-family: "Roboto", sans-serif;
    color: var(--white);
  }
  .contact .person {
    font-family: "Exo 2", sans-serif;
    font-weight: 600;
    font-size: 27px;
    color: var(--green);
    line-height: 1.05;
  }
  .contact .role { font-size: 15px; margin-bottom: 12px; }
  .contact .line {
    display: flex; align-items: center; gap: 9px;
    font-size: 15px; line-height: 22px;
    white-space: nowrap;
  }
  .contact .icon {
    width: 15px; height: 15px; border-radius: 50%;
    background: var(--green);
    display: flex; align-items: center; justify-content: center;
    flex: none;
  }
  .contact .address { font-size: 15px; line-height: 20px; margin-top: 6px; }
  .edge-strip {
    position: absolute;
    left: 0; bottom: 0;
    width: 300px; height: 22px;
    background: var(--grey);
  }
  .web-band {
    position: absolute;
    right: 0; bottom: 0;
    width: 380px; height: 66px;
    background: var(--green);
    border-top-left-radius: 40px;
    display: flex; align-items: center;
    padding-left: 56px;
    font-family: "Roboto", sans-serif;
    font-size: 16px;
    color: var(--white);
  }
</style>
</head>
<body>
  <section class="card front">
    <div class="brand">
      <div class="brand-name">brovix</div>
      <div class="brand-tag">ELECTRICAL WHOLESALERS</div>
    </div>
  </section>

  <section class="card back">
    <div class="brand">
      <div class="brand-row">
        <div class="brand-name">brovix</div>
        <div class="brand-mark"></div>
      </div>
      <div class="brand-tag">ELECTRICAL WHOLESALERS</div>
    </div>

    <div class="contact">
      <div class="person">Halyna Dorosh</div>
      <div class="role">Director of Marketing</div>
      <div class="line">
        <span class="icon">
          <svg width="9" height="9" viewBox="0 0 10 10"><path d="M2 1 L4 3 L3 4 Q4.5 6 6 7 L7 6 L9 8 L8 9.3 Q4 9 0.8 2 Z" fill="#232323"/></svg>
        </span>
        780.555.0184
      </div>
      <div class="line">
        <span class="icon">
          <svg width="9" height="9" viewBox="0 0 10 10"><rect x="1" y="2.5" width="8" height="5.5" fill="none" stroke="#232323" stroke-width="1.2"/><path d="M1 2.5 L5 5.5 L9 2.5" fill="none" stroke="#232323" stroke-width="1.2"/></svg>
        </span>
        halya.dorosh@quillmail.example
      </div>
      <div class="address">20517 - 87 Ave. Edmonton,<br>AB, Canada T6K 4N8</div>
    </div>

    <div class="edge-strip"></div>
    <div class="web-band">www.brovix.example</div>
  </section>
</body>
</html>
```